Business Card Design

We are a commercial real estate brokerage in San Francisco, leasing office buildings downtown.
I would like a clean, elegant look. Simple but powerful .

Industry/Entity Type

Business

Contact Information for Business Card

Derek Holloway
lic# 07258143
415.555.0172
derek@velt-commercial.example
velt-commercial.example

```html
<!DOCTYPE html>
<html lang="en">
<head>
<meta charset="utf-8">
<title>Velt Commercial – Business Card</title>
<link rel="stylesheet" href="https://fonts.googleapis.com/css2?family=Open+Sans:wght@400;600;700&display=swap">
<style>
  :root {
    --canvas: #e4e2df;
    --card-dark: #0f1012;
    --card-light: #ededed;
    --brand-blue: #6f86a8;
    --slate: #585b5f;
    --ink: #1f2022;
    --ink-soft: #3a3c3f;
    --rule: #cfcfcf;
    --lic-text: #c9ccd0;
  }
  * { margin: 0; padding: 0; box-sizing: border-box; }
  html, body {
    width: 1200px; height: 768px; overflow: hidden;
    background: var(--canvas);
    font-family: "Open Sans", Arial, sans-serif;
  }
  .stage { position: relative; width: 1200px; height: 768px; }

  .card {
    position: absolute; top: 234px;
    width: 520px; height: 300px;
    border-radius: 3px; overflow: hidden;
    box-shadow: 0 6px 18px rgba(0,0,0,0.18);
  }

  /* Back of card */
  .card-back { left: 50px; background: var(--card-dark); }
  .card-back .wordmark {
    position: absolute; left: 0; right: 0; top: 104px;
    text-align: center; color: var(--brand-blue); font-weight: 700;
    line-height: 1;
  }
  .wordmark .wordmark-main { display: block; font-size: 56px; letter-spacing: 2px; }
  .wordmark .wordmark-sub { display: block; font-size: 22px; letter-spacing: 3px; margin-top: 6px; }

  /* Front of card */
  .card-front { left: 630px; background: var(--card-light); }
  .card-front .wordmark {
    position: absolute; left: 24px; width: 230px; top: 92px;
    text-align: center; color: var(--brand-blue); font-weight: 700; line-height: 1;
  }
  .card-front .wordmark .wordmark-main { font-size: 50px; }
  .card-front .wordmark .wordmark-sub { font-size: 20px; }

  .divider {
    position: absolute; left: 272px; top: 40px;
    width: 1px; height: 190px; background: var(--rule);
  }

  .contact { position: absolute; left: 296px; top: 76px; }
  .contact .name { font-size: 22px; font-weight: 700; color: var(--ink); letter-spacing: 0.3px; }
  .contact .role { font-size: 12px; color: var(--ink-soft); margin-top: -2px; }
  .contact-list { list-style: none; margin-top: 18px; }
  .contact-list li {
    display: flex; align-items: center; gap: 9px;
    font-size: 13.5px; color: var(--ink); height: 23px;
  }
  .contact-list svg { width: 12px; height: 12px; flex: none; }

  .bands { position: absolute; left: 0; bottom: 0; width: 520px; height: 60px; }
  .license {
    position: absolute; left: 300px; bottom: 15px;
    font-size: 13px; color: var(--lic-text); letter-spacing: 0.5px;
  }
</style>
</head>
<body>
<main class="stage">

  <section class="card card-back" aria-label="Business card back">
    <div class="wordmark">
      <span class="wordmark-main">VELT</span>
      <span class="wordmark-sub">COMMERCIAL</span>
    </div>
  </section>

  <section class="card card-front" aria-label="Business card front">
    <div class="wordmark">
      <span class="wordmark-main">VELT</span>
      <span class="wordmark-sub">COMMERCIAL</span>
    </div>

    <div class="divider"></div>

    <div class="contact">
      <p class="name">Derek Holloway</p>
      <p class="role">Managing Director</p>
      <ul class="contact-list">
        <li>
          <svg viewBox="0 0 12 12" aria-hidden="true"><path fill="var(--brand-blue)" d="M1 3.2C1 2 2.2 1.5 6 1.5s5 .5 5 1.7v1H8.3V3.3H3.7v.9H1zM3 5h6l1.8 5.5H1.2z"/><circle cx="6" cy="7.6" r="1.3" fill="var(--card-light)"/></svg>
          415.555.0172
        </li>
        <li>
          <svg viewBox="0 0 12 12" aria-hidden="true"><rect x="0.5" y="2.5" width="11" height="7.5" fill="var(--brand-blue)"/><path d="M0.8 2.8 6 7l5.2-4.2" fill="none" stroke="var(--card-light)" stroke-width="1"/></svg>
          derek@velt-commercial.example
        </li>
        <li>
          <svg viewBox="0 0 12 12" aria-hidden="true"><circle cx="6" cy="6" r="5.2" fill="var(--brand-blue)"/><path d="M1 6h10M6 .8c-2.4 2.8-2.4 7.6 0 10.4M6 .8c2.4 2.8 2.4 7.6 0 10.4" fill="none" stroke="var(--card-light)" stroke-width="0.8"/></svg>
          velt-commercial.example
        </li>
      </ul>
    </div>

    <svg class="bands" viewBox="0 0 520 60" aria-hidden="true">
      <polygon points="0,28 250,28 280,60 0,60" fill="var(--brand-blue)"/>
      <polygon points="232,10 520,10 520,60 276,60" fill="var(--slate)"/>
    </svg>
    <p class="license">LIC# 07258143</p>
  </section>

</main>
</body>
</html>
```